I am starting a company that will help small businesses that are looking to raise money over the internet (i.e. crowd fund) in reliance of the JOBS Act and the new rules that have been recently passed.

Initially, the website will help a business figure out if it is qualified to raise money and if so, it will tell the business what information is required.

The various pages will need to gather information from the businesses through Yes/No questionnaires, drop-down lists and free text boxes -

I am still thinking about my company's name and don't have a logo - for now, please use the name "MLAH (marble lantern advisory hub)" - feel free to throw in an idea for a logo

Hi all - I was wondering if I could get some design suggestions that don't use stock photos- thanks

Based on the designs I have received so far, I don't think the description of my website is clear.  The website will NOT be a crowdfunding portal (i.e. it is not like plumvesta etc.)  It is an information website that will allow companies to determine if they are legally able to raise money online. 

If they are able to raise money online, then the company can sign-up for some paid services which include legal documents and agreements.

To help the design process, I've uploaded a draft of the questions that a company will need to answer to determine if it is able to raise money online.

The submitted designs should be for both the homepage as well as the pages on which the questions will be set out.

Thanks for taking the time to read.

small businesses that will be looking to raise money through crowd funding

Internet

• I need designs for the following pages:

1. Home page
- should be simple - links to 'about' page and 'blog' page
- room at the bottom for affiliate links/logos
- convey the message that there are many rules that need to be followed to legally crowd fund a company but that this website makes compliance easy
- prominent 'get started' button

2. Company questions pages
- laid out to ask ~ 5 questions:
- name of company (free text answer)
- amount raised in prior 12 months (drop down box)
- state of formation (drop down box)
- registered with the ODV (y/n)
- registered as an investment company (y/n)

- needs to be a help 'icon' beside the questions so that user can hover over the icon and get more information as to what the question is asking

3. Eligibility questions page
- list of ~25 questions (y/n) answers
-
4. Fund raising objectives page
- list of ~15 questions answers
- answers will be y/n, multiple choice, drop down menu or free text

5. Results page
- if company is not-eligible to proceed, display "Not Eligible" page with list of reasons why
- if company is eligible, display "Congratulations" page with link to "Sign-up and Continue"

6. Sign-up page
- name
- address
- e-mail etc.
- check box to agree to terms and conditions

7. 'blog' page

8. about / disclaimer page

```html
<!DOCTYPE html>
<html lang="en">
<head>
<meta charset="utf-8">
<title>Marble Lantern Advisory Hub</title>
<link href="https://fonts.googleapis.com/css2?family=Open+Sans:wght@400;600;700&display=swap" rel="stylesheet">
<style>
:root{
  --green:#2fae5c;
  --green-light:#5fc67c;
  --green-text:#2a9d55;
  --orange:#f0a01e;
  --red:#c8162e;
  --ink:#333;
  --muted:#777;
  --line:#e3e3e3;
  --footer:#2a2a2a;
  --footer-deep:#1c1c1c;
  --blue:#2a8fd6;
}
*{box-sizing:border-box;margin:0;padding:0}
html,body{width:1200px;height:2696px;overflow:hidden}
body{font-family:"Open Sans",Arial,sans-serif;color:var(--ink);background:#fff;position:relative}

.site-header{position:absolute;left:0;top:0;width:1200px;height:112px;background:#fff}
.brand{position:absolute;left:88px;top:34px;display:flex;align-items:center;gap:16px}
.brand-mark{width:52px;height:52px;border-radius:50%;background:var(--green)}
.brand-name{font-size:30px;font-weight:600;color:var(--ink)}
.login{position:absolute;right:88px;top:20px;width:96px;height:36px;background:var(--orange);color:#fff;font-size:15px;font-weight:600;display:flex;align-items:center;justify-content:center}
.main-nav{position:absolute;right:88px;top:82px;display:flex;gap:40px;font-size:17px;color:#555}

.hero{position:absolute;left:0;top:112px;width:1200px;height:400px;background:linear-gradient(120deg,var(--green),var(--green-light))}
.hero-title{position:absolute;left:88px;top:72px;width:540px;color:#fff;font-size:40px;line-height:50px;font-weight:600}
.hero-sub{position:absolute;left:88px;top:130px;width:540px;color:#e4f7ea;font-size:26px}
.hero-copy{position:absolute;left:88px;top:180px;width:520px;color:#e8f8ee;font-size:16px;line-height:24px}
.get-started{position:absolute;left:88px;top:268px;width:200px;height:52px;background:var(--orange);color:#fff;font-size:18px;font-weight:700;display:flex;align-items:center;justify-content:center}
.hero-dots{position:absolute;left:88px;top:352px;display:flex;gap:8px}
.hero-dots span{width:12px;height:12px;border-radius:50%;background:rgba(255,255,255,.5)}
.hero-dots span:first-child{background:#fff}
.hero-visual{position:absolute;left:660px;top:40px;width:452px;height:328px;background:linear-gradient(#fdfdf6,#f1efe2);border:6px solid #fff}

.section-title{position:absolute;left:88px;font-size:24px;font-weight:700;color:var(--green-text)}

.pick-video{position:absolute;left:88px;top:640px;width:440px;height:212px;background:linear-gradient(#5a4a3a,#2a221a)}
.pick-video .play{position:absolute;left:196px;top:82px}
.pick-info{position:absolute;left:580px;top:632px;width:280px}
.pick-info h3{color:var(--green-text);font-size:18px;font-weight:600}
.pick-info p{font-size:16px;color:#555;line-height:24px;margin-top:4px}
.stats{display:flex;justify-content:space-between;font-size:13px;font-weight:700;color:#555;margin-top:16px}
.bar{height:6px;background:#ddd;margin-top:6px;position:relative}
.bar i{position:absolute;left:0;top:0;height:6px;background:var(--red)}
.categories{position:absolute;left:880px;top:600px;width:232px;list-style:none;font-size:15px;color:#444;line-height:32px}
.divider{position:absolute;left:88px;width:1024px;height:1px;background:var(--line)}

.card{position:absolute;width:300px;height:412px;border:1px solid var(--line);box-shadow:0 2px 6px rgba(0,0,0,.12);padding:8px;background:#fff}
.card-img{width:282px;height:190px}
.card h4{color:var(--green-text);font-size:16px;font-weight:600;margin-top:14px}
.card .meta{display:flex;align-items:center;gap:6px;font-size:13px;color:var(--muted);margin-top:6px}
.card p{font-size:14px;line-height:22px;color:#555;margin-top:14px;height:66px}
.card .rule{height:1px;background:var(--line);margin-top:16px}
.card .stats{margin-top:12px}

.success-visual{position:absolute;left:88px;top:2088px;width:452px;height:272px;background:radial-gradient(ellipse at center,#8fb07a,#5b9ad6 70%,#eaf2fa)}
.success-text{position:absolute;left:620px;top:2092px;width:492px}
.success-text h3{font-size:24px;font-weight:400;color:#666}
.success-text p{font-size:14px;line-height:22px;color:#777;margin-top:14px}

.site-footer{position:absolute;left:0;top:2392px;width:1200px;height:304px;background:var(--footer);color:#ccc}
.footer-col{position:absolute;top:40px}
.footer-col h5{font-size:16px;color:#fff;font-weight:600;margin-bottom:12px}
.footer-col ul{list-style:none;font-size:14px;line-height:26px}
.social{display:flex;gap:10px}
.social span{width:36px;height:36px;background:var(--blue)}
.social span:nth-child(3){background:var(--orange)}
.social span:nth-child(4){background:var(--red)}
.newsletter p{font-size:14px;line-height:22px;color:#eee;width:264px}
.newsletter .field{width:264px;height:36px;background:#fff;margin-top:14px}
.newsletter .subscribe{width:128px;height:36px;background:var(--blue);color:#fff;font-size:15px;display:flex;align-items:center;justify-content:center;margin-top:16px;margin-left:136px}
.copyright{position:absolute;left:0;bottom:0;width:1200px;height:44px;background:var(--footer-deep);font-size:13px;color:#aaa;padding:13px 88px}
</style>
</head>
<body>
<header class="site-header">
  <div class="brand"><span class="brand-mark"></span><span class="brand-name">Marble Lantern Advisory Hub</span></div>
  <div class="login">LOGIN</div>
  <nav class="main-nav"><span>ABOUT</span><span>LEARN</span><span>BLOG</span></nav>
</header>

<section class="hero">
  <h1 class="hero-title">Crowdfunding has rules.</h1>
  <p class="hero-sub">We make compliance easy.</p>
  <p class="hero-copy">Answer a few simple questions to find out if your company can legally raise money online, and exactly what information you will need.</p>
  <div class="get-started">GET STARTED</div>
  <div class="hero-dots"><span></span><span></span><span></span><span></span></div>
  <div class="hero-visual" role="img" aria-label="Illustration of a light bulb with a dollar sign above a colourful crowd"></div>
</section>

<h2 class="section-title" style="top:592px">OUR PICK OF THE WEEK</h2>
<div class="pick-video" role="img" aria-label="Video still for a short guide to crowdfunding rules">
  <svg class="play" width="48" height="48" viewBox="0 0 48 48"><circle cx="24" cy="24" r="24" fill="rgba(0,0,0,.45)"/><path d="M19 14l14 10-14 10z" fill="#fff"/></svg>
</div>
<div class="pick-info">
  <h3>The Rules in 3 Minutes</h3>
  <p>A short guide to the JOBS Act<br>and what it means for you.</p>
  <div class="stats"><span>VIDEO GUIDE</span><span>3 MIN</span></div>
  <div class="bar"><i style="width:58%"></i></div>
</div>
<ul class="categories">
  <li>COMPANY QUESTIONS</li><li>ELIGIBILITY</li><li>FUND RAISING GOALS</li><li>RESULTS</li><li>SIGN-UP</li><li>LEGAL DOCUMENTS</li><li>BLOG</li><li>ABOUT / DISCLAIMER</li>
</ul>
<div class="divider" style="top:888px"></div>

<h2 class="section-title" style="top:928px">CHECK YOUR ELIGIBILITY</h2>
<article class="card" style="left:88px;top:980px">
  <div class="card-img" role="img" aria-label="Photo of a small business team at work" style="background:linear-gradient(#8a6a58,#3c2e28)"></div>
  <h4>Company questions</h4>
  <div class="meta"><svg width="14" height="14" viewBox="0 0 14 14"><circle cx="7" cy="7" r="7" fill="#999"/><path d="M4 7l2 2 4-4" stroke="#fff" stroke-width="1.6" fill="none"/></svg>Step 1 · about 2 minutes</div>
  <p>Your company name, amount raised in the prior 12 months, state of formation and registrations.</p>
  <div class="rule"></div>
  <div class="stats"><span>STEP 1</span><span>5 QUESTIONS</span></div>
  <div class="bar"><i style="width:33%"></i></div>
</article>
<article class="card" style="left:448px;top:980px">
  <div class="card-img" role="img" aria-label="Photo of people reviewing documents" style="background:linear-gradient(#c8b8a2,#6b5c4c)"></div>
  <h4>Eligibility questions</h4>
  <div class="meta"><svg width="14" height="14" viewBox="0 0 14 14"><circle cx="7" cy="7" r="7" fill="#999"/><path d="M4 7l2 2 4-4" stroke="#fff" stroke-width="1.6" fill="none"/></svg>Step 2 · simple yes or no</div>
  <p>A short list of yes or no questions that shows if you are able to raise money online.</p>
  <div class="rule"></div>
  <div class="stats"><span>STEP 2</span><span>25 QUESTIONS</span></div>
  <div class="bar"><i style="width:66%"></i></div>
</article>
<article class="card" style="left:808px;top:980px">
  <div class="card-img" role="img" aria-label="Photo of a founder planning goals" style="background:linear-gradient(#9aa4a8,#4e5558)"></div>
  <h4>Fund raising objectives</h4>
  <div class="meta"><svg width="14" height="14" viewBox="0 0 14 14"><circle cx="7" cy="7" r="7" fill="#999"/><path d="M4 7l2 2 4-4" stroke="#fff" stroke-width="1.6" fill="none"/></svg>Step 3 · about 5 minutes</div>
  <p>Tell us how much you want to raise and how, using lists, choices and free text.</p>
  <div class="rule"></div>
  <div class="stats"><span>STEP 3</span><span>15 QUESTIONS</span></div>
  <div class="bar"><i style="width:100%"></i></div>
</article>

<h2 class="section-title" style="top:1484px">AFTER YOUR ANSWERS</h2>
<article class="card" style="left:88px;top:1532px">
  <div class="card-img" role="img" aria-label="Photo of a laptop showing results" style="background:linear-gradient(#7c8088,#34373c)"></div>
  <h4>See your results</h4>
  <div class="meta"><svg width="14" height="14" viewBox="0 0 14 14"><circle cx="7" cy="7" r="7" fill="#999"/><path d="M4 7l2 2 4-4" stroke="#fff" stroke-width="1.6" fill="none"/></svg>Instant answer</div>
  <p>Find out right away if you are eligible, with a clear list of reasons either way.</p>
  <div class="rule"></div>
  <div class="stats"><span>RESULTS</span><span>FREE</span></div>
  <div class="bar"><i style="width:100%"></i></div>
</article>
<article class="card" style="left:448px;top:1532px">
  <div class="card-img" role="img" aria-label="Photo of a team signing up together" style="background:linear-gradient(#6e665e,#2c2824)"></div>
  <h4>Sign-up and continue</h4>
  <div class="meta"><svg width="14" height="14" viewBox="0 0 14 14"><circle cx="7" cy="7" r="7" fill="#999"/><path d="M4 7l2 2 4-4" stroke="#fff" stroke-width="1.6" fill="none"/></svg>For eligible companies</div>
  <p>Create your account with your name, address and e-mail to unlock paid services.</p>
  <div class="rule"></div>
  <div class="stats"><span>SIGN-UP</span><span>2 MINUTES</span></div>
  <div class="bar"><i style="width:50%"></i></div>
</article>
<article class="card" style="left:808px;top:1532px">
  <div class="card-img" role="img" aria-label="Photo of legal documents on a desk" style="background:linear-gradient(135deg,#c04a3a,#3a6ab0 50%,#e0b040)"></div>
  <h4>Legal documents</h4>
  <div class="meta"><svg width="14" height="14" viewBox="0 0 14 14"><circle cx="7" cy="7" r="7" fill="#999"/><path d="M4 7l2 2 4-4" stroke="#fff" stroke-width="1.6" fill="none"/></svg>Paid services</div>
  <p>Get the agreements and filings you need, prepared from the answers you gave us.</p>
  <div class="rule"></div>
  <div class="stats"><span>DOCUMENTS</span><span>READY TO USE</span></div>
  <div class="bar"><i style="width:75%"></i></div>
</article>

<h2 class="section-title" style="top:2032px">FEATURED SUCCESS STORY</h2>
<div class="success-visual" role="img" aria-label="Illustration of a circle of people around a stack of banknotes"></div>
<div class="success-text">
  <h3>Featured Success Stories</h3>
  <p>Mara Lindqvist runs a small design studio that wanted to raise money online. Our questions showed her studio was eligible in under ten minutes.</p>
  <p>With her results in hand, she signed up, received her legal documents and agreements, and launched a fully compliant raise with confidence.</p>
</div>

<footer class="site-footer">
  <div class="footer-col" style="left:88px">
    <h5>Quick Links</h5>
    <ul><li>Get Started</li><li>Company Questions</li><li>Eligibility Questions</li><li>Fund Raising Objectives</li><li>Sign-up</li></ul>
  </div>
  <div class="footer-col" style="left:348px">
    <h5>About</h5>
    <ul><li>About us</li><li>Blog</li><li>Help</li><li>Disclaimer</li><li>Terms Of Service</li></ul>
  </div>
  <div class="footer-col" style="left:580px">
    <h5>Follow us on</h5>
    <div class="social"><span></span><span></span><span></span><span></span></div>
  </div>
  <div class="footer-col newsletter" style="left:848px">
    <p>Stay in touch with us by signing up for our quarterly newsletter!</p>
    <div class="field"></div>
    <div class="subscribe">SUBSCRIBE</div>
  </div>
  <div class="copyright">Copyright ©2013. All Rights Reserved.</div>
</footer>
</body>
</html>
```